Letter and Envelope Design For Harborline Realty

Please design a letter and an envelope incorporating our logo (See Attached). We are also launched a business card contest. Since we want them to match, please feel free to submit a design for both the business card and also the letter design and envelope.

Requirements
Must have
• The envelope, the letter and the business cards must match somehow connecting the designs. We want them to have something that holds them together besides the logo.

```html
<!DOCTYPE html>
<html lang="en">
<head>
<meta charset="utf-8">
<title>Harborline Realty – Letterhead and Envelope</title>
<link href="https://fonts.googleapis.com/css2?family=Source+Sans+3:wght@400;600&display=swap" rel="stylesheet">
<style>
  :root{
    --navy:#041a8a;
    --paper:#fafafa;
    --ink:#4a4a4a;
    --ink-dark:#222;
    --stage:#e4e4e4;
    --rule:#c8c8c8;
  }
  *{box-sizing:border-box;margin:0;padding:0}
  html,body{width:1200px;height:825px;overflow:hidden;background:var(--stage)}
  .canvas{position:relative;width:1200px;height:825px}

  .sheet{position:absolute;background:var(--paper);overflow:hidden;box-shadow:0 2px 6px rgba(0,0,0,.12)}
  .sheet .art{position:absolute;left:0;top:0;width:100%;height:100%}
  .base-band{position:absolute;left:0;right:0;bottom:0;background:var(--navy)}

  .contact{position:absolute;text-align:right;color:#fff;font-family:"Source Sans 3",sans-serif;font-size:8.6px;line-height:11.2px}
  .contact li{list-style:none;display:flex;justify-content:flex-end;align-items:center;gap:3px}
  .contact .dot{width:7px;height:7px;border-radius:50%;background:#fff;display:inline-block}
  .contact .addr{margin-top:2px;display:block}

  .brand-name{position:absolute;text-align:center;color:var(--navy);font-family:"Source Sans 3",sans-serif;font-weight:600;white-space:nowrap;letter-spacing:.5px}

  /* Letter */
  .letter{left:80px;top:82px;width:467px;height:660px}
  .letter .contact{right:40px;top:12px}
  .letter .brand-name{left:22px;top:96px;width:160px;font-size:16px}
  .letter .base-band{height:10px}
  .letter-body{position:absolute;left:42px;top:155px;width:383px;color:var(--ink);font-family:"Source Sans 3",sans-serif;font-size:10px;line-height:12.3px;letter-spacing:-.1px}
  .salutation{font-family:Arial,sans-serif;font-weight:700;font-size:11px;color:var(--ink-dark);margin-bottom:16px;letter-spacing:0}
  .letter-body p{text-align:justify;margin-bottom:12.3px}
  .signature{position:absolute;left:42px;top:502px;width:74px;height:36px;background:linear-gradient(90deg,#d8d8d8,#ececec);border-radius:3px}

  /* Envelope */
  .envelope{left:583px;top:442px;width:537px;height:298px;background:transparent;box-shadow:none}
  .envelope .art{filter:drop-shadow(0 2px 3px rgba(0,0,0,.12))}
  .envelope .contact{right:48px;top:74px}
  .envelope .brand-name{left:37px;top:140px;width:160px;font-size:15px}
  .envelope .base-band{height:8px}
  .address-box{position:absolute;left:33px;top:200px;width:205px;height:64px;background:#fff;border-radius:4px;box-shadow:0 0 2px rgba(0,0,0,.08);font-family:"Source Sans 3",sans-serif;font-size:7px;color:var(--ink)}
  .address-box .to{position:absolute;left:7px;top:5px}
  .address-box .line{position:absolute;left:7px;right:7px;border-top:1px dotted var(--rule)}
</style>
</head>
<body>
<main class="canvas">

  <section class="sheet letter">
    <svg class="art" viewBox="0 0 584 825" preserveAspectRatio="none" aria-hidden="true">
      <path fill="var(--navy)" d="M0 0H584V82C560 100 532 113 500 113C400 113 330 62 230 50C150 42 62 62 0 120Z"/>
      <path fill="none" stroke="#fff" stroke-width="6" stroke-linecap="round" d="M58 46C130 16 222 16 300 44C380 74 462 104 552 108"/>
    </svg>
    <ul class="contact">
      <li>555-014-2290 <span class="dot"></span></li>
      <li>info@harborlinerealty.com <span class="dot"></span></li>
      <li>www.harborlinerealty.com <span class="dot"></span></li>
      <li class="addr">Po. box 201, Street Name,<br>City Name, Zip Code - 00000</li>
    </ul>
    <p class="brand-name">Harborline Realty</p>
    <div class="letter-body">
      <p class="salutation">Dear Mr. Carter,</p>
      <p>Lorem Ipsum is simply dummy text of the printing and typesetting industry. Lorem Ipsum has been the industry's standard dummy text ever since the 1500s, when an unknown printer took a galley of type and scrambled it to make a type specimen book. It has survived not only five centuries, but also the leap into electronic typesetting, remaining essentially unchanged.</p>
      <p>The standard chunk of Lorem Ipsum used since the 1500s is reproduced below for those interested. Sections 1.10.32 and 1.10.33 from "de Finibus Bonorum et Malorum" by Orvel are also reproduced in their exact original form, accompanied by English versions from the 1914 translation by H. Arden</p>
      <p>Lorem Ipsum is simply dummy text of the printing and typesetting industry. Lorem Ipsum has been the industry's standard dummy text ever since the 1500s, when an unknown printer took a galley of type and scrambled it to make a type specimen book. It has survived not only five centuries, but also the leap into electronic typesetting, remaining essentially unchanged. It was popularised in the</p>
      <p>The standard chunk of Lorem Ipsum used since the 1500s is reproduced below for those interested. Sections 1.10.32 and 1.10.33 from "de Finibus Bonorum et Malorum" by Orvel are also reproduced in their exact original form, accompanied by English versions from the 1914 translation by H. Arden</p>
      <p>The standard chunk of Lorem Ipsum used since the 1500s is reproduced below for those interested. Sections 1.10.32 and 1.10.33 from "de Finibus Bonorum et Malorum" by Orvel are</p>
    </div>
    <div class="signature" role="img" aria-label="Handwritten signature"></div>
    <div class="base-band"></div>
  </section>

  <section class="sheet envelope">
    <svg class="art" viewBox="0 0 671 372" preserveAspectRatio="none" aria-hidden="true">
      <rect x="0" y="78" width="671" height="294" fill="var(--paper)"/>
      <path fill="var(--navy)" d="M0 80L9 18Q12 0 30 0H641Q659 0 662 18L671 80V155C650 176 620 190 580 191C480 192 380 122 250 107C160 97 60 122 0 210Z"/>
      <line x1="0" y1="80" x2="671" y2="80" stroke="rgba(255,255,255,.18)" stroke-dasharray="2 2"/>
      <path fill="none" stroke="#fff" stroke-width="6" stroke-linecap="round" d="M68 120C140 92 230 90 320 118C420 150 520 186 630 190"/>
    </svg>
    <ul class="contact">
      <li>555-014-2290 <span class="dot"></span></li>
      <li>info@harborlinerealty.com <span class="dot"></span></li>
      <li>www.harborlinerealty.com <span class="dot"></span></li>
      <li class="addr">Po. box 201, Street Name,<br>City Name, Zip Code - 00000</li>
    </ul>
    <p class="brand-name">Harborline Realty</p>
    <div class="address-box">
      <span class="to">To</span>
      <span class="line" style="top:16px"></span>
      <span class="line" style="top:30px"></span>
      <span class="line" style="top:43px"></span>
      <span class="line" style="top:57px"></span>
    </div>
    <div class="base-band"></div>
  </section>

</main>
</body>
</html>
```